"Harbor Builders" is a residential building company and needs a new business card design and may re

We would like a redesign based on the existing logo, and would like to see a new font as well. We are bespoke home builders who build sustainable energy efficient homes.

Industry/Entity Type

Construction

Contact Information for Business Card

Business card size 40mm x 90mm

Colors

Designer to choose colors to be used in the design.

```html
<!DOCTYPE html>
<html lang="en">
<head>
<meta charset="utf-8">
<title>Harbor Builders – Business Card</title>
<link href="https://fonts.googleapis.com/css2?family=Work+Sans:wght@400;500;600&display=swap" rel="stylesheet">
<style>
  :root {
    --canvas-bg: #2a2a2c;
    --card-bg: #1e1e1f;
    --card-edge: #262627;
    --orange: #f08421;
    --blue: #2c4495;
    --ink: #e6e6e6;
    --muted: #8e8e90;
  }
  * { margin: 0; padding: 0; box-sizing: border-box; }
  html, body { width: 1200px; height: 900px; overflow: hidden; }
  body {
    background: var(--canvas-bg);
    font-family: "Work Sans", Arial, sans-serif;
    position: relative;
  }
  .card {
    position: absolute;
    left: 170px;
    width: 860px;
    height: 382px;
    background: var(--card-bg);
    border: 1px solid var(--card-edge);
    box-shadow: 0 12px 30px rgba(0,0,0,.45);
  }
  .card--front { top: 40px; }
  .card--back { top: 470px; }

  .front-brand {
    position: absolute;
    left: 0; right: 0; top: 160px;
    display: flex; align-items: center; justify-content: center; gap: 18px;
  }
  .front-brand__square {
    width: 44px; height: 44px;
    border: 3px solid var(--muted);
  }
  .front-brand__name {
    font-size: 40px; font-weight: 500; letter-spacing: 4px;
    color: var(--muted); text-transform: uppercase;
  }

  .back-brand {
    position: absolute;
    left: 60px; top: 120px; width: 330px;
    display: flex; align-items: center; gap: 16px;
  }
  .back-brand__square { width: 52px; height: 52px; background: var(--orange); flex: none; }
  .back-brand__name {
    font-size: 34px; font-weight: 600; line-height: 1.1; color: var(--orange);
  }
  .divider {
    position: absolute; left: 420px; top: 56px;
    width: 3px; height: 236px; background: var(--orange);
  }
  .details { position: absolute; left: 450px; top: 50px; color: var(--ink); }
  .details__name {
    font-size: 26px; font-weight: 500; color: var(--blue);
    text-transform: uppercase; letter-spacing: .5px;
  }
  .details__role { font-size: 19px; margin-bottom: 16px; }
  .details__reg { font-size: 18px; line-height: 1.3; }
  .details__label { color: var(--orange); }
  .details__address { font-size: 18px; line-height: 1.3; margin: 14px 0 12px; }
  .contact { list-style: none; font-size: 18px; line-height: 1.55; }
  .contact li { display: flex; align-items: center; gap: 14px; }
  .contact svg { width: 16px; height: 16px; flex: none; }
  .contact__accent { color: var(--orange); }
</style>
</head>
<body>
  <section class="card card--front" aria-label="Card front">
    <div class="front-brand">
      <span class="front-brand__square"></span>
      <span class="front-brand__name">Harbor Builders</span>
    </div>
  </section>

  <section class="card card--back" aria-label="Card back">
    <div class="back-brand">
      <span class="back-brand__square"></span>
      <span class="back-brand__name">Harbor Builders</span>
    </div>
    <div class="divider"></div>
    <div class="details">
      <p class="details__name">Daniel Moretti</p>
      <p class="details__role">Founder</p>
      <p class="details__reg"><span class="details__label">Registration</span>-40871</p>
      <p class="details__reg"><span class="details__label">ABN:</span> 12 345 678 910</p>
      <p class="details__address">PO Box 2210 Northgate<br>LPO Bayview WA 6001</p>
      <ul class="contact">
        <li>
          <svg viewBox="0 0 16 16" aria-hidden="true"><path d="M3 2l3 3-1.5 2a9 9 0 0 0 4.5 4.5L11 10l3 3-2 2C6 15 1 10 1 4z" fill="var(--orange)"/></svg>
          0400 123 987
        </li>
        <li>
          <svg viewBox="0 0 16 16" aria-hidden="true"><rect x="1" y="3" width="14" height="10" fill="var(--orange)"/><path d="M1 3l7 6 7-6" fill="none" stroke="var(--card-bg)" stroke-width="1.5"/></svg>
          daniel@harborbuilders.com.au
        </li>
        <li>
          <svg viewBox="0 0 16 16" aria-hidden="true" fill="none" stroke="var(--orange)" stroke-width="1.4"><circle cx="8" cy="8" r="6.5"/><ellipse cx="8" cy="8" rx="3" ry="6.5"/><path d="M1.5 8h13M2.5 4.5h11M2.5 11.5h11"/></svg>
          <span>www.<span class="contact__accent">harborbuilders.com</span>.au</span>
        </li>
      </ul>
    </div>
  </section>
</body>
</html>
```